Marwick Law Letterhead

We need a new letterhead design for a Law Firm. The address for the law firm is 1475 Calloway Street, Suite 210, Houston, Texas 77041. Phone Number: 832-361-9027; Fax Number: 832-614-7359. The logo is uploaded to the project.

```html
<!DOCTYPE html>
<html lang="en">
<head>
<meta charset="utf-8">
<title>Marwick Law Letterhead</title>
<link rel="stylesheet" href="https://fonts.googleapis.com/css2?family=Cormorant+Garamond:wght@600&family=Arimo:wght@400&display=swap">
<style>
  :root {
    --backdrop: #dfe3e3;
    --paper: #f3f3f2;
    --navy: #132a5c;
    --red: #d0121c;
    --white: #ffffff;
  }
  * { margin: 0; padding: 0; box-sizing: border-box; }
  html, body {
    width: 1200px;
    height: 960px;
    overflow: hidden;
    background: var(--backdrop);
  }
  .letterhead {
    position: absolute;
    left: 289px;
    top: 40px;
    width: 622px;
    height: 880px;
    background: var(--paper);
    box-shadow: 0 2px 10px rgba(0,0,0,0.12);
    overflow: hidden;
  }
  .brand {
    position: absolute;
    left: 44px;
    top: 43px;
    display: flex;
    align-items: center;
    gap: 10px;
  }
  .brand-dot {
    width: 26px;
    height: 26px;
    border-radius: 50%;
    background: var(--navy);
  }
  .brand-name {
    font-family: "Cormorant Garamond", Georgia, serif;
    font-weight: 600;
    font-size: 30px;
    letter-spacing: 0.5px;
    color: var(--navy);
    line-height: 1;
  }
  .footer-band-red {
    position: absolute;
    left: 88px;
    right: 0;
    top: 848px;
    height: 12px;
    background: var(--red);
  }
  .footer-band-navy {
    position: absolute;
    left: 60px;
    right: 0;
    top: 867px;
    height: 13px;
    background: var(--navy);
  }
  .corner-disc {
    position: absolute;
    left: 0;
    top: 774px;
    width: 96px;
    height: 96px;
    border-radius: 50%;
    background: var(--navy);
    border: 4px solid var(--paper);
  }
  .contact-line {
    position: absolute;
    top: 848px;
    height: 12px;
    display: flex;
    align-items: center;
    font-family: "Arimo", Arial, sans-serif;
    font-size: 8px;
    color: var(--white);
    white-space: nowrap;
  }
  .contact-address { left: 171px; }
  .contact-phone { left: 420px; gap: 4px; }
  .contact-fax { left: 513px; gap: 4px; }
  .contact-line svg { width: 8px; height: 8px; fill: var(--white); }
</style>
</head>
<body>
  <main class="letterhead">
    <header class="brand">
      <span class="brand-dot"></span>
      <span class="brand-name">Marwick Law</span>
    </header>

    <footer class="letterhead-footer">
      <div class="footer-band-red"></div>
      <div class="footer-band-navy"></div>
      <div class="corner-disc"></div>
      <span class="contact-line contact-address">1475 Calloway Street, Suite 210, Houston, Texas 77041</span>
      <span class="contact-line contact-phone">
        <svg viewBox="0 0 24 24" aria-hidden="true"><path d="M6.6 10.8a15.1 15.1 0 0 0 6.6 6.6l2.2-2.2a1 1 0 0 1 1-.25 11.4 11.4 0 0 0 3.6.6 1 1 0 0 1 1 1V20a1 1 0 0 1-1 1A17 17 0 0 1 3 4a1 1 0 0 1 1-1h3.5a1 1 0 0 1 1 1c0 1.25.2 2.45.6 3.6a1 1 0 0 1-.25 1z"/></svg>
        832 361 9027
      </span>
      <span class="contact-line contact-fax">
        <svg viewBox="0 0 24 24" aria-hidden="true"><path d="M7 2h10v5H7zM4 8h16a2 2 0 0 1 2 2v7h-4v5H6v-5H2v-7a2 2 0 0 1 2-2zm4 8v4h8v-4z"/></svg>
        832 614 7359
      </span>
    </footer>
  </main>
</body>
</html>
```